A5 Patient Information Booklet (Chiropractic Clinic) 4-8 pages

Here’s a polished, professional rewrite of your full brief and content, with clearer structure, corrected language, and a premium tone:

---

**Project Title:** Premium Patient Information Brochure (Chiropractic & Wellness Clinic)

---

### **Overview**

We are a health and wellness clinic seeking a premium, high-end patient information brochure to provide following a patient’s initial consultation and first treatment.

The purpose of this booklet is to:

* Reinforce trust and professionalism
* Help patients understand what to expect next
* Encourage adherence to care recommendations
* Position the clinic as calm, expert-led, and results-driven

---

### **Format**

* 4–8 page booklet (A5 or similar size)
* Print-ready and digital versions required

---

### **Target Audience**

Patients who have just completed their initial consultation and may have begun treatment. They may already be experiencing physical or mental changes, so the brochure should guide, reassure, and educate them on what comes next.

---

### **Tone & Style**

* Premium, calm, and reassuring
* Modern wellness aesthetic (not overly clinical)
* Clean layout with minimal clutter
* Soft, neutral colour palette (whites, creams, muted greens, soft blues)
* Elegant typography (e.g. Montserrat / Lato)
* High-end, trustworthy, and professional feel

---

### **Key Messages**

#### 1. Listen to Your Body

Patients may feel different after treatment. Reassure them that this is normal and part of the healing process.

#### 2. Post-Treatment Advice

* Stay well hydrated
* Rest if needed
* Avoid overexertion if the body requires recovery

#### 3. Healing is a Journey (Core Concept)

A strong visual metaphor of a **“road to recovery”** or **journey** should be central to the design.

This journey should clearly illustrate three phases:

* **Phase 1: Initial Care (Weeks 1–6)**
Focus: Reducing pain/discomfort, calming the body, and initiating response to treatment

* **Phase 2: Corrective Care (Weeks 6–12)**
Focus: Addressing underlying issues, improving function, and creating lasting change

* **Phase 3: Wellness / Maintenance (Ongoing)**
Focus: Maintaining progress, preventing relapse, and supporting long-term wellbeing

**Important:**

* Emphasise that this is not a quick fix
* Progress requires time and consistency
* Each patient follows an individualised care plan
* The journey should feel structured, positive, and achievable

#### 4. Personalised Care

Reinforce that every treatment plan is tailored specifically to the individual.

#### 5. Professional Reassurance

Patients should feel confident they are in expert hands and supported throughout their journey.

---

### **Design Direction**

* Use imagery that reflects calmness, progression, and wellness (e.g. pathways, nature, soft gradients)
* Avoid generic stock imagery
* **Only use original clinic images from website and social media**
* Prioritise white space and clarity
* Aim for a luxury spa/medical hybrid aesthetic

---

## **Content Structure (Page-by-Page)**

### **Front Cover**

* Clean, minimal, premium design
* Clinic branding

---

### **Page 1: Patient Case Summary**

**Title:** *Welcome to Fernwell Spine Studio*

Thank you for choosing Fernwell Spine Studio.

This booklet is designed to guide you through:

* What we found during your initial consultation
* Your personalised recommended treatment plan
* Your road to recovery
* Long-term wellness care
* Why we take the approach we do

---

### **Page 2: Your Care Journey**

**Stage 1: Your Initial Consultation**

Today we completed a comprehensive assessment of your health and function, including:

* Full case history and discussion of your symptoms and goals
* Orthopaedic and neurological testing
* Postural and movement assessment
* Initial treatment (where appropriate)

**What this tells us:**

* How your body is currently functioning
* Where areas of stress or dysfunction may be present
* The most appropriate and effective path forward for your care

---

### **Page 3: Your Suggested Treatment Plan**

Based on today’s findings, your recommended care plan is:

**______ treatments over ______ weeks**

This should be viewed alongside your *Road to Recovery* to help you understand what to expect.

We have also discussed:

* Expected timelines for improvement
* Available payment options

**After Treatment:**
It is common to feel different following treatment. This is a normal response as your body begins to adapt and respond.

We recommend:

* Staying well hydrated
* Allowing time for rest and recovery
* Avoiding overexertion if your body feels it needs it

---

### **Page 4: What to Expect Next**

Healing is not always linear—it is a process that occurs over time.

Your care will typically progress through the following stages:

* **Relief Care**
Focused on reducing discomfort and calming the body

* **Corrective Care**
Focused on addressing underlying issues and improving function
(This phase may include prescribed exercises)

* **Maintenance / Wellness Care**
Focused on sustaining progress, preventing recurrence, and supporting long-term health

---

### **Page 5: Understanding Chiropractic Care**

**What is Chiropractic?**
Chiropractic care focuses on the relationship between the spine, nervous system, and overall body function.

By improving spinal movement and alignment, chiropractic care helps support the nervous system, allowing the body to function and heal more effectively.

**About Fernwell Spine Studio**
At Fernwell Spine Studio, our approach is centred around personalised, patient-focused care. We aim to not only relieve symptoms but to address underlying causes and support long-term wellbeing.

---

### **Back Page**

* Clinic contact details
* Website
* Social media icons/handles

**Closing Message:**
“A healthier, stronger you—supported every step of the way.”

---

### **Deliverables**

* Print-ready PDF
* Editable source files

---

### **Additional Notes**

* The brochure should feel valuable and worth keeping
* Encourage long-term care in a subtle, non-pushy way
* Maintain clarity, readability, and strong visual hierarchy
* Balance professionalism with warmth and approachability

---

If you’d like, I can also turn this into **actual brochure copy (fully written, patient-facing text)** or help you refine it further for a designer.

Existing patients who want to feel better and look after themselves that is given after their initil consultation appointment

Chiropractic, wellness, health

• Montserrat or Lato

0094D4
00A9DD
6FCCEA
C7EBF8
E9F6FB
00AB8E
00BBA5
67D7C9
C6EFE9
E9F9F6
6B429C
8869AF
B7A5CE
E3DAEB
F3F0F8

• my own photos, look premium wellness, be clear and simple to understand for patients journey or what to expect next and over time
• USe my social media/website for ideas
• generic photos and images

```html
<!DOCTYPE html>
<html lang="en">
<head>
<meta charset="utf-8">
<title>Fernwell Spine Studio – Patient Booklet</title>
<link href="https://fonts.googleapis.com/css2?family=Libre+Baskerville:ital,wght@0,400;0,700;1,400;1,700&family=Lato:ital,wght@0,400;0,700;1,400&display=swap" rel="stylesheet">
<style>
:root{
  --bg:#c8c8c8;
  --paper:#f7f7f8;
  --teal:#1aa79b;
  --teal-deep:#14958b;
  --teal-soft:#67d7c9;
  --teal-mist:#c6efe9;
  --navy:#23304a;
  --ink:#3b4350;
  --purple:#8869af;
  --lilac:#b7a5ce;
  --lilac-mist:#e3daeb;
  --orange:#ef7b3a;
  --amber:#f1b233;
  --green:#8cbf3f;
  --serif:"Libre Baskerville",Georgia,serif;
  --sans:"Lato",Arial,sans-serif;
}
*{box-sizing:border-box;margin:0;padding:0}
html,body{width:1200px;height:2580px;overflow:hidden}
body{background:var(--bg);font-family:var(--sans);color:var(--ink);position:relative}
.spread{position:absolute;left:50px;width:1100px;height:778px;display:flex;box-shadow:0 10px 30px rgba(0,0,0,.18)}
.spread--covers{top:60px}
.spread--welcome{top:901px}
.spread--recovery{top:1742px}
.page{position:relative;width:550px;height:778px;overflow:hidden;background:var(--paper)}
.page>*{position:absolute}
.photo{background:linear-gradient(135deg,#d9cfc6,#a7a2a4 55%,#6f7d92)}
.photo--teal{background:linear-gradient(135deg,#46b6ab,#1f9e94)}
.heading{font-family:var(--serif);font-weight:700;color:var(--navy);font-size:21px;line-height:1.15}
.heading em{display:block;color:var(--teal);font-style:italic;font-weight:700}
.heading--light{color:#fff}
.heading--light em{color:#fff}
.sub{font-weight:700;font-size:11.5px;color:var(--navy)}
.copy{font-size:11px;line-height:1.45}
.copy--light{color:#fff}
.bullets{list-style:none;font-size:11px;line-height:1.5}
.bullets li::before{content:"•";margin-right:6px;color:var(--navy)}
.ticks{list-style:none;font-size:11px;line-height:1.6;color:#fff}
.ticks li::before{content:"✓";display:inline-block;width:12px;height:12px;line-height:12px;border-radius:50%;background:#fff;color:var(--teal);font-size:8px;text-align:center;margin-right:6px}
.ring{width:28px;height:28px;border-radius:50%;border:1.5px solid var(--purple);box-shadow:inset 0 0 0 3px #fff,inset 0 0 0 4px var(--teal-soft);flex:none}
.icon-list{list-style:none;display:flex;flex-direction:column;gap:10px}
.icon-list li{display:flex;align-items:center;gap:10px;font-size:11px;line-height:1.3}

/* covers */
.back-cover{background:var(--teal)}
.back-cover .photo--teal{left:0;top:0;width:550px;height:430px;opacity:.55}
.back-intro{left:80px;top:150px;width:390px;text-align:center;color:#fff;font-size:11px;line-height:1.5}
.plan-title{left:0;width:550px;top:292px;text-align:center;font-family:var(--serif);font-weight:700;color:#fff;font-size:19px}
.plan-card{left:60px;top:330px;width:430px;height:230px;background:#f4f4f5;border-radius:18px;padding:26px 30px;font-family:var(--serif);color:var(--navy);font-size:14px;line-height:2}
.blank{display:inline-block;border-bottom:1px solid var(--navy);vertical-align:baseline}
.plan-card p.note{font-family:var(--sans);color:var(--teal);font-size:12px;line-height:1.4;text-align:center;margin-top:12px}
.contact{left:0;width:550px;top:600px;text-align:center;color:#fff}
.contact h3{font-family:var(--serif);font-size:19px;margin-bottom:10px}
.contact p{font-family:var(--serif);font-size:11px;line-height:1.8}
.front-cover{background:linear-gradient(215deg,#d6bde8 0%,#e9e1f1 35%,#f4f5f8 60%,#e3f4f2 100%)}
.cover-title{left:0;width:550px;top:170px;text-align:center;font-family:var(--serif);font-weight:700;color:var(--navy);font-size:30px;line-height:1.3}
.cover-title span{color:var(--teal)}
.brand{left:0;width:550px;top:330px;display:flex;align-items:center;justify-content:center;gap:12px}
.brand-dot{width:22px;height:22px;border-radius:50%;background:var(--teal)}
.brand-name{font-family:var(--serif);font-weight:700;font-size:24px;color:var(--navy)}
.cover-tag{left:60px;width:430px;top:420px;text-align:center;font-family:var(--serif);font-weight:700;color:var(--navy);font-size:16px;line-height:1.5}
.cover-motto{left:0;width:550px;top:505px;display:flex;align-items:center;justify-content:center;gap:10px;color:var(--teal);font-size:18px}
.cover-motto i{display:block;width:60px;height:1px;background:var(--teal);position:relative}
.cover-motto i::after{content:"";position:absolute;top:-3px;width:7px;height:7px;border-radius:50%;background:var(--teal)}
.cover-motto i:first-child::after{right:0}
.cover-motto i:last-child::after{left:0}

/* welcome spread */
.feature-row{left:40px;top:190px;display:flex;gap:12px}
.feature{width:80px;height:86px;border:1px solid #d3d6dc;border-radius:10px;background:#fff;display:flex;flex-direction:column;align-items:center;padding-top:10px;gap:6px;text-align:center;font-size:8.5px;line-height:1.2}
.curve-band{left:0;bottom:0;width:550px}
.oval-photo{border-radius:50%}
.pill-row{display:flex;gap:40px}
.pill{display:flex;align-items:center;gap:8px;font-size:10px;line-height:1.3;width:170px}

/* recovery */
.stage{width:140px;font-size:10.5px;line-height:1.35}
.stage strong{display:block;font-size:11px;margin-bottom:4px}
.stage .label{font-family:var(--serif);font-size:11px;margin-bottom:4px}
</style>
</head>
<body>

<!-- Spread 1: back cover + front cover -->
<section class="spread spread--covers">
  <article class="page back-cover">
    <div class="photo photo--teal" role="img" aria-label="Faded portrait of the chiropractor, tinted teal"></div>
    <p class="back-intro">Your Chiropractor At Fernwell Spine Studio, your care is led by chiropractor Maren, who takes a personalised, hands-on approach to your health. Every consultation is focused on understanding your body, your lifestyle, and your goals—so your treatment plan is tailored specifically to you. Maren combines clinical expertise with a calm, supportive environment to help you feel confident, informed, and in control of your recovery journey.</p>
    <h2 class="plan-title">Your Personalised Plan</h2>
    <div class="plan-card">
      <p>Patient Name: <span class="blank" style="width:230px"></span></p>
      <p>Your Suggested Care Plan:</p>
      <p><span class="blank" style="width:70px"></span> treatments over <span class="blank" style="width:70px"></span> weeks</p>
      <p class="note">Your care has been designed specifically for your needs, goals, and current condition. We’re here to support you throughout your journey—with professional guidance, experience, and ongoing care.</p>
    </div>
    <div class="contact">
      <h3>Contact us:</h3>
      <p>12 Alder Row, Thornbury, United Kingdom</p>
      <p>hello@fernwellspine.co.uk</p>
      <p>www.fernwellspine.co.uk</p>
    </div>
  </article>
  <article class="page front-cover">
    <h1 class="cover-title">Your Journey to<br>Better Health <span>Starts Here</span></h1>
    <div class="brand"><span class="brand-dot"></span><span class="brand-name">FERNWELL SPINE STUDIO</span></div>
    <p class="cover-tag">A personalised approach to recovery, balance, and long-term wellbeing.</p>
    <p class="cover-motto"><i></i>Guided care. Lasting results.<i></i></p>
  </article>
</section>

<!-- Spread 2: welcome + treatment plan -->
<section class="spread spread--welcome">
  <article class="page">
    <h2 class="heading" style="left:40px;top:45px">Welcome to<em>Fernwell Spine Studio</em></h2>
    <p class="copy" style="left:40px;top:110px;width:450px">Thank you for choosing Fernwell Spine Studio. We’re delighted to support you on your journey toward improved health and wellbeing. This booklet has been designed to guide you through what comes next and to help you feel confident in your care.<br>Inside, you’ll find:</p>
    <div class="feature-row">
      <div class="feature"><span class="ring"></span>A summary of your initial consultation</div>
      <div class="feature"><span class="ring"></span>Your tailored treatment plan</div>
      <div class="feature"><span class="ring"></span>What to expect during your recovery</div>
      <div class="feature"><span class="ring"></span>Guidance for after your treatment</div>
      <div class="feature"><span class="ring"></span>Our long-term approach to wellness</div>
    </div>
    <p class="copy" style="left:40px;top:300px;width:460px">Our goal is simple — to help you feel better, move better, and live better.</p>
    <div class="photo" style="left:20px;top:380px;width:240px;height:340px;border-radius:12px" role="img" aria-label="Chiropractor assessing a seated patient's posture"></div>
    <h2 class="heading" style="left:290px;top:370px">Your<em>Care Journey</em></h2>
    <p class="sub" style="left:290px;top:430px">Your First Visit: What We Assessed</p>
    <p class="copy" style="left:290px;top:450px;width:230px">During your initial consultation, we carried out a detailed assessment of your health and body function, including:</p>
    <ul class="icon-list" style="left:290px;top:520px;width:230px">
      <li><span class="ring"></span>A full discussion of your symptoms, concerns, and goals</li>
      <li><span class="ring"></span>Orthopaedic and neurological testing</li>
      <li><span class="ring"></span>Postural and movement analysis</li>
      <li><span class="ring"></span>Initial treatment (where appropriate)</li>
    </ul>
  </article>
  <article class="page">
    <p class="sub" style="left:50px;top:45px">What This Means for You</p>
    <p class="copy" style="left:50px;top:66px;width:430px">This process helps us understand:</p>
    <ul class="bullets" style="left:50px;top:84px;width:430px">
      <li>How your body is currently functioning</li>
      <li>Where stress, imbalance, or dysfunction may exist</li>
      <li>The most effective and personalised path forward</li>
    </ul>
    <p class="copy" style="left:50px;top:136px;width:330px">Every recommendation we make is based on your unique needs.</p>
    <div class="photo oval-photo" style="left:390px;top:190px;width:250px;height:250px;border:5px solid var(--lilac)" role="img" aria-label="Chiropractor treating a patient's arm in the clinic"></div>
    <h2 class="heading" style="left:50px;top:190px">Your<em>Treatment Plan</em></h2>
    <p class="copy" style="left:50px;top:250px;width:330px">Based on your assessment, your recommended care plan is:<br><span class="blank" style="width:40px"></span> treatments over <span class="blank" style="width:40px"></span> weeks</p>
    <p class="copy" style="left:50px;top:300px;width:330px">This plan is carefully designed to support your recovery and guide your progress step by step.</p>
    <p class="copy" style="left:50px;top:340px">We have also discussed:</p>
    <div class="pill-row" style="left:50px;top:365px">
      <div class="pill"><span class="ring"></span>Expected timelines for improvement</div>
      <div class="pill"><span class="ring"></span>Flexible payment options</div>
    </div>
    <svg class="curve-band" height="340" viewBox="0 0 550 340" aria-hidden="true">
      <path d="M0 40 C150 -10 300 0 420 40 C480 60 520 50 550 35 L550 340 L0 340Z" fill="var(--lilac-mist)"/>
      <path d="M0 52 C150 2 300 12 420 52 C480 72 520 62 550 47 L550 340 L0 340Z" fill="var(--teal)"/>
    </svg>
    <h2 class="heading heading--light" style="left:50px;top:470px">After<em>Your Treatment</em></h2>
    <p class="copy copy--light" style="left:50px;top:530px;width:320px">It is completely normal to feel different after treatment. Your body is beginning to respond and adapt — this is part of the healing process.</p>
    <p class="sub" style="left:50px;top:580px;color:#fff">We Recommend:</p>
    <ul class="ticks" style="left:50px;top:598px;width:300px">
      <li>Staying well hydrated</li>
      <li>Allowing time for rest and recovery</li>
      <li>Avoiding overexertion if your body feels fatigued</li>
    </ul>
    <p class="copy copy--light" style="left:50px;top:670px;width:320px">Listening to your body is key during this stage.</p>
    <div class="photo oval-photo" style="left:340px;top:600px;width:300px;height:230px" role="img" aria-label="Chiropractor checking a patient's spine"></div>
  </article>
</section>

<!-- Spread 3: road to recovery + care phases -->
<section class="spread spread--recovery">
  <article class="page">
    <h2 class="heading" style="left:40px;top:45px">Your Road<em>To Recovery</em></h2>
    <p class="sub" style="left:40px;top:105px">Healing is a Journey</p>
    <p class="copy" style="left:40px;top:123px;width:460px">Recovery doesn’t happen overnight. It is a gradual and structured process, unique to every individual.<br>Your care typically progresses through three key stages:</p>
    <svg style="left:20px;top:185px" width="510" height="130" viewBox="0 0 510 130" aria-hidden="true">
      <defs><linearGradient id="road" x1="0" x2="1"><stop offset="0" stop-color="#ef7b3a"/><stop offset=".5" stop-color="#f1b233"/><stop offset="1" stop-color="#8cbf3f"/></linearGradient></defs>
      <path d="M5 40 C60 20 90 20 120 30 C170 50 180 90 230 90 C300 90 320 60 370 60 C420 60 440 90 500 80" fill="none" stroke="url(#road)" stroke-width="6" stroke-linecap="round"/>
      <circle cx="110" cy="28" r="20" fill="#fff" stroke="var(--orange)" stroke-width="2"/>
      <circle cx="245" cy="88" r="20" fill="#fff" stroke="var(--amber)" stroke-width="2"/>
      <circle cx="390" cy="60" r="20" fill="#fff" stroke="var(--green)" stroke-width="2"/>
    </svg>
    <div class="stage" style="left:60px;top:250px"><p class="label" style="color:var(--orange)">Relief Care</p><strong>Weeks 1–6</strong>Focus: Reducing discomfort, calming the body, and initiating healing</div>
    <div class="stage" style="left:200px;top:310px"><p class="label" style="color:var(--amber)">Corrective Care</p><strong>Weeks 6–12</strong>Focus: Addressing underlying issues, improving movement, and restoring function (This phase may include exercises and corrective strategies)</div>
    <div class="stage" style="left:350px;top:280px"><p class="label" style="color:var(--green)">Wellness &amp; Maintenance</p><strong>Ongoing</strong>Focus: Maintaining progress, preventing relapse, &amp; supporting long-term health</div>
    <div class="photo" style="left:-60px;top:500px;width:340px;height:260px;border-radius:0 50% 50% 0" role="img" aria-label="Patient lying on a treatment table during an adjustment"></div>
    <h2 class="heading" style="left:300px;top:520px">What To<em>Expect Next</em></h2>
    <p class="sub" style="left:300px;top:580px">Understanding Your Progress</p>
    <p class="copy" style="left:300px;top:600px;width:220px">Healing is not always linear. Some days you may feel significant improvement, while others may feel slower — this is completely normal. What matters most is steady progress over time.</p>
  </article>
  <article class="page">
    <div class="photo oval-photo" style="left:-40px;top:40px;width:220px;height:220px;border:5px solid var(--lilac)" role="img" aria-label="Chiropractor examining a patient's back"></div>
    <h2 class="heading" style="left:220px;top:60px;font-size:20px">Your Care <span style="color:var(--teal);font-style:italic">Phases Explained</span></h2>
    <ul class="icon-list" style="left:220px;top:110px;width:280px;gap:18px">
      <li><span class="ring"></span><span><b class="sub">Relief Care</b><br>Focused on easing discomfort and reducing tension</span></li>
      <li><span class="ring"></span><span><b class="sub">Corrective Care</b><br>Focused on long-term improvements and fixing root causes</span></li>
      <li><span class="ring"></span><span><b class="sub">Wellness Care</b><br>Focused on maintaining results and supporting ongoing health</span></li>
    </ul>
    <svg class="curve-band" height="470" viewBox="0 0 550 470" aria-hidden="true">
      <path d="M0 60 C140 0 300 10 420 55 C480 78 520 70 550 55 L550 470 L0 470Z" fill="var(--lilac-mist)"/>
      <path d="M0 74 C140 14 300 24 420 69 C480 92 520 84 550 69 L550 470 L0 470Z" fill="var(--teal)"/>
      <ellipse cx="200" cy="420" rx="150" ry="90" fill="var(--teal-soft)" opacity=".35"/>
    </svg>
    <h2 class="heading heading--light" style="left:50px;top:390px">What is<em>Chiropractic Care?</em></h2>
    <p class="copy copy--light" style="left:50px;top:450px;width:440px">Chiropractic care focuses on the connection between your spine, nervous system, and overall body function. When spinal movement and alignment improve, your nervous system can function more effectively — helping your body heal and perform at its best.</p>
    <h2 class="heading heading--light" style="left:50px;top:530px">Our Approach at<em>Fernwell Spine Studio</em></h2>
    <p class="copy copy--light" style="left:50px;top:585px">At Fernwell Spine Studio, we believe in:</p>
    <ul class="ticks" style="left:50px;top:603px;width:260px">
      <li>Personalised, patient-focused care</li>
      <li>Treating the root cause — not just symptoms</li>
      <li>Supporting long-term health and wellbeing</li>
    </ul>
    <p class="copy copy--light" style="left:50px;top:670px;width:250px">You’re not just receiving treatment — you’re investing in your future health.</p>
    <div class="photo" style="left:320px;top:560px;width:230px;height:218px;border-radius:50% 0 0 0" role="img" aria-label="Chiropractor supporting a smiling patient during treatment"></div>
  </article>
</section>

</body>
</html>
```